Brivane Management

We need a web design for a new consulting company, with clients all over the world. The company provides management consulting to the travel industry.

Logo files are attached.

Website must look very corporate and be responsive in design.

Management Consulting

```html
<!DOCTYPE html>
<html lang="en">
<head>
<meta charset="utf-8">
<title>Brivane Management</title>
<link rel="stylesheet" href="https://fonts.googleapis.com/css2?family=Lato:wght@400;700&family=Lora:wght@400&family=Bitter:wght@400&family=Oswald:wght@300&display=swap">
<style>
:root{
  --navy:#15184a;
  --green:#5aa21e;
  --blue:#0a6fc9;
  --footer:#0a6bc3;
  --footer-dark:#0857a6;
  --button-dark:#06509b;
  --band:#ececec;
  --text:#333;
  --rule:#d9d9d9;
  --white:#fff;
}
*{margin:0;padding:0;box-sizing:border-box}
html,body{width:756px;height:1200px;overflow:hidden;background:var(--white)}
body{position:relative;font-family:"Lato",sans-serif;color:var(--text)}
h1,h2,h3,h4{font-weight:400}
a{text-decoration:none}
.abs{position:absolute}
.site-header{top:0;left:0;width:756px;height:65px;background:var(--white)}
.brand-name{left:83px;top:22px;font-family:"Lato",sans-serif;font-weight:700;font-size:19px;line-height:22px;color:var(--navy)}
.nav-link{top:30px;font-family:"Lora",serif;font-size:8.5px;line-height:10px;color:var(--navy)}
.nav-sep{top:30px;width:1px;height:10px;background:var(--rule)}
.hero{top:65px;left:0;width:756px;height:298px;background:linear-gradient(90deg,#8fa9b5 0%,#a7c1cb 35%,#6f8791 52%,#2a2e33 68%,#3c4247 85%,#a9c6d3 100%)}
.hero-title{top:178px;left:82px;font-family:"Oswald",sans-serif;font-weight:300;font-size:19.5px;line-height:28.5px;color:var(--white)}
.section-title{left:0;width:756px;text-align:center;font-family:"Lora",serif;font-size:20px;color:var(--navy);letter-spacing:1px}
.section-sub{left:0;width:756px;text-align:center;font-size:9.5px;font-weight:700;color:var(--green);letter-spacing:1px}
.rule{left:83px;width:590px;height:1px;background:var(--rule)}
.intro{left:88px;width:580px;text-align:center;font-size:8.3px;line-height:12.5px}
.intro-lead{font-weight:700;color:#222}
.btn{display:block;background:var(--blue);color:var(--white);font-size:8.5px;text-align:center;line-height:20px;height:20px}
.services-band{top:582px;left:0;width:756px;height:213px;background:var(--band)}
.service-card{top:600px;width:138px;height:177px;background:var(--white);padding:2px}
.service-photo{height:76px}
.service-title{margin-top:10px;text-align:center;font-family:"Bitter",serif;font-size:12px;color:var(--navy);letter-spacing:.3px}
.service-text{margin-top:7px;text-align:center;font-size:8px;line-height:13px}
.service-card .btn{width:66px;margin:9px auto 0}
.quote{top:894px;width:268px;height:74px;border:1px solid var(--rule);border-radius:4px;background:var(--white);margin:0}
.quote-tail{left:24px;bottom:-12px;width:16px;height:12px}
.avatar{left:10px;top:10px;width:54px;height:54px;border-radius:50%;border:2px solid var(--white);box-shadow:0 0 0 1px var(--rule)}
.quote-text{left:74px;top:14px;width:186px;font-size:8px;line-height:12.5px;text-indent:14px}
.quote-mark{left:74px;top:10px;font-family:"Lora",serif;font-size:18px;color:#bbb}
.client{top:990px;font-size:8.5px;font-weight:700;color:var(--navy)}
.site-footer{top:1028px;left:0;width:756px;height:145px;background:var(--footer);color:var(--white)}
.footer-title{top:14px;font-family:"Bitter",serif;font-size:11.5px}
.footer-rule{top:35px;height:1px;background:rgba(255,255,255,.25)}
.footer-line{font-size:8px;line-height:11px;display:flex;align-items:center;gap:7px}
.social-dot{width:15px;height:15px;border-radius:50%;background:var(--white)}
.email-field{top:75px;left:393px;width:127px;height:20px;background:var(--white);border-radius:2px;color:#888;font-size:7.5px;line-height:20px;padding-left:6px}
.subscribe{top:104px;left:393px;width:61px;height:20px;background:var(--button-dark);font-size:8px;line-height:20px;text-align:center}
.copyright{top:1173px;left:0;width:756px;height:27px;background:var(--footer-dark);color:var(--white);font-size:8px;line-height:27px;text-align:center}
</style>
</head>
<body>

<header class="site-header abs">
  <div class="brand-name abs">Brivane Management</div>
  <nav>
    <a class="nav-link abs" href="#" style="left:396px">HOME</a>
    <span class="nav-sep abs" style="left:440px"></span>
    <a class="nav-link abs" href="#" style="left:460px">ABOUT US</a>
    <span class="nav-sep abs" style="left:521px"></span>
    <a class="nav-link abs" href="#" style="left:541px">SERVICES</a>
    <span class="nav-sep abs" style="left:601px"></span>
    <a class="nav-link abs" href="#" style="left:620px">CONTACT US</a>
  </nav>
</header>

<section class="hero abs" role="img" aria-label="Businessman in a suit sketching an airplane outline with a pen over a light blue background"></section>
<h1 class="hero-title abs">WE PROVIDES MANAGEMENT<br>CONSULTING TO THE<br>TRAVEL INDUSTRY.</h1>

<section>
  <h2 class="section-title abs" style="top:391px">WELCOME BRIVANE</h2>
  <p class="section-sub abs" style="top:418px">STRATEGY MANAGEMENT, INC.</p>
  <div class="rule abs" style="top:440px"></div>
  <p class="intro intro-lead abs" style="top:453px">Lorem ipsum dolor sit amet, consectetur adipisicing elit, sed do eiusmod tem incididunt ut labore et dolore magna aliqua. Ut enim ad minim veniam.</p>
  <p class="intro abs" style="top:473px">Duis aute irure dolor in reprehenderitnin voliuptate velit esse cillum dolore eu fugiat nulla pariatur Excepteur sint occaecat cupidatat non proident, sunt in culpa qui officia deserunt mollit anim id est laborum Neque porro quisquam est, qui dolorem ipsum qus consectetur adipisci velit, sed quia non numquam eius modi tempora incidunt ut labore et dol magnam aliquam quaerat voluptatem. Ut enim ad minima veniam, quis nostrum exer ullam corporis suscipit laboriosam nisi ut aliquid ex ea commodi consequatur.</p>
  <a class="btn abs" href="#" style="top:533px;left:346px;width:65px">READ MORE</a>
</section>

<section class="services-band abs"></section>
<article class="service-card abs" style="left:83px">
  <div class="service-photo" role="img" aria-label="Business people shaking hands in an office" style="background:linear-gradient(135deg,#c9d6e3,#2c3a55 60%,#dfe6ee)"></div>
  <h3 class="service-title">Account Management</h3>
  <p class="service-text">Duis aute irure dolor in rderi<br>voliuptate velit esse.</p>
  <a class="btn" href="#">READ MORE</a>
</article>
<article class="service-card abs" style="left:233px">
  <div class="service-photo" role="img" aria-label="Row of business travellers standing with luggage" style="background:linear-gradient(180deg,#e9ecef,#5b5f66 55%,#cfd3d8)"></div>
  <h3 class="service-title">Traveller Tools</h3>
  <p class="service-text">Duis aute irure dolor in rderi<br>voliuptate velit esse.</p>
  <a class="btn" href="#">READ MORE</a>
</article>
<article class="service-card abs" style="left:384px">
  <div class="service-photo" role="img" aria-label="Calculator, pen and financial chart in blue tones" style="background:linear-gradient(135deg,#3d6fb0,#a9c4e6 55%,#e8f0fa)"></div>
  <h3 class="service-title">Expense Management</h3>
  <p class="service-text">Duis aute irure dolor in rderi<br>voliuptate velit esse.</p>
  <a class="btn" href="#">READ MORE</a>
</article>
<article class="service-card abs" style="left:535px">
  <div class="service-photo" role="img" aria-label="Traveller pulling a suitcase through an airport terminal" style="background:linear-gradient(180deg,#dfe9f2,#8fa6bb 60%,#4f6477)"></div>
  <h3 class="service-title">Travel Programs</h3>
  <p class="service-text">Duis aute irure dolor in rderi<br>voliuptate velit esse.</p>
  <a class="btn" href="#">READ MORE</a>
</article>

<section>
  <h2 class="section-title abs" style="top:822px">CLIENT TESTIMONIALS</h2>
  <p class="section-sub abs" style="top:849px">NEQUE PORRO QUISQUA MOLOREM</p>
  <div class="rule abs" style="top:872px"></div>

  <blockquote class="quote abs" style="left:100px">
    <svg class="quote-tail abs" viewBox="0 0 16 12"><path d="M0 0 L8 12 L16 0" fill="#fff" stroke="#d9d9d9"/></svg>
    <div class="avatar abs" role="img" aria-label="Client portrait" style="background:linear-gradient(135deg,#e8cdb5,#b98a60)"></div>
    <span class="quote-mark abs">&ldquo;</span>
    <p class="quote-text abs">Lorem ipsu donlor amet, consecte admsicn elt sed do eiusmod tempor incididunt utboret dolorie magna aliqua. Ut enim ad minienia quis nosinttrud exercitation ullamco laboriisi.</p>
  </blockquote>
  <p class="client abs" style="left:100px">Miss. Client Name</p>

  <blockquote class="quote abs" style="left:388px">
    <svg class="quote-tail abs" viewBox="0 0 16 12"><path d="M0 0 L8 12 L16 0" fill="#fff" stroke="#d9d9d9"/></svg>
    <div class="avatar abs" role="img" aria-label="Client portrait" style="background:linear-gradient(135deg,#e4e6ea,#7b8592)"></div>
    <span class="quote-mark abs">&ldquo;</span>
    <p class="quote-text abs">Lorem ipsu donlor amet, consecte admsicn elt sed do eiusmod tempor incididunt utboret dolorie magna aliqua. Ut enim ad minienia quis nosinttrud exercitation ullamco laboriisi.</p>
  </blockquote>
  <p class="client abs" style="left:388px">Mr. Client Name</p>
</section>

<footer class="site-footer abs">
  <h4 class="footer-title abs" style="left:83px">Quick Links</h4>
  <div class="footer-rule abs" style="left:83px;width:97px"></div>
  <div class="footer-line abs" style="left:83px;top:44px"><svg width="7" height="7" viewBox="0 0 7 7"><path d="M0 3.5H6M3.5 1L6 3.5L3.5 6" stroke="#fff" fill="none"/></svg>Home</div>
  <div class="footer-line abs" style="left:83px;top:66px"><svg width="7" height="7" viewBox="0 0 7 7"><path d="M0 3.5H6M3.5 1L6 3.5L3.5 6" stroke="#fff" fill="none"/></svg>About Us</div>
  <div class="footer-line abs" style="left:83px;top:87px"><svg width="7" height="7" viewBox="0 0 7 7"><path d="M0 3.5H6M3.5 1L6 3.5L3.5 6" stroke="#fff" fill="none"/></svg>Services</div>
  <div class="footer-line abs" style="left:83px;top:108px"><svg width="7" height="7" viewBox="0 0 7 7"><path d="M0 3.5H6M3.5 1L6 3.5L3.5 6" stroke="#fff" fill="none"/></svg>Contact Us</div>

  <h4 class="footer-title abs" style="left:208px">Contact Information</h4>
  <div class="footer-rule abs" style="left:208px;width:157px"></div>
  <svg class="abs" style="left:208px;top:44px" width="8" height="11" viewBox="0 0 8 11"><path d="M4 0a4 4 0 0 1 4 4c0 3-4 7-4 7S0 7 0 4a4 4 0 0 1 4-4z" fill="#fff"/><circle cx="4" cy="4" r="1.5" fill="#0a6bc3"/></svg>
  <p class="abs" style="left:227px;top:44px;font-size:8px;line-height:12px"><b>BRIVANE</b><br>00 Neque porro quisquam &nbsp;dolor<br>qus consectetur. 000 000</p>
  <svg class="abs" style="left:208px;top:89px" width="9" height="11" viewBox="0 0 9 11"><path d="M2 0h2l1 3-1.5 1c.5 1.5 1.5 2.5 3 3L7.5 5.5 9 7v2c-1 1-2 1-3 .5C3 8 1 6 .5 3 0 1.5 1 0 2 0z" fill="#fff"/></svg>
  <p class="abs" style="left:227px;top:90px;font-size:8px">(123) 456 7890</p>
  <svg class="abs" style="left:208px;top:111px" width="10" height="7" viewBox="0 0 10 7"><rect width="10" height="7" fill="#fff"/><path d="M0 0l5 4 5-4" stroke="#0a6bc3" fill="none"/></svg>
  <p class="abs" style="left:227px;top:109px;font-size:8px">info@brivanemgmt.com</p>

  <h4 class="footer-title abs" style="left:393px">Newsletter Sign Up</h4>
  <div class="footer-rule abs" style="left:393px;width:135px"></div>
  <p class="abs" style="left:393px;top:44px;width:135px;font-size:7.5px;line-height:12px">Lorem ipsudolor sit coec adipiscing elitsite amet</p>
  <div class="email-field abs">Your Email</div>
  <div class="subscribe abs">SUBSCRIBE</div>

  <h4 class="footer-title abs" style="left:561px">Follow Us</h4>
  <div class="footer-rule abs" style="left:561px;width:110px"></div>
  <div class="footer-line abs" style="left:564px;top:47px;gap:10px"><span class="social-dot"></span>Friendwall</div>
  <div class="footer-line abs" style="left:564px;top:70px;gap:10px"><span class="social-dot"></span>Chirpline</div>
  <div class="footer-line abs" style="left:564px;top:93px;gap:10px"><span class="social-dot"></span>Circleplus</div>
</footer>
<p class="copyright abs">&copy; 2014 Brivane. All Right reserved.</p>

</body>
</html>
```